New business card for a regional office of a US M&A company

We need business card for a finance company, office based in Hong Kong , our Head office is in US, our business is to Merge and acquires companies , the new office will be a regional office for the Asia Pacific region. We want to use the head office logo as attached ( but don't have to be exactly the same, can be a variation to it) as a base and then add Asia Pacific alongside the logo.
We would prefer to have be bilingual Eng + Chinese, although we don't really have Chinese company name .

Industry/Entity Type

Business

Contact Information for Business Card

Clara Jo Tsang
 

VP,
APAC M&A Operations
Orin Vantage Asia Pacific Limited
 
Unit 1407, K18
18 Tai Lok Shan Road, 
Hong Kong 
 
M: +852 6038 1742
T : +852 2836 4100
F : +852 2836 4177
VOIP: 4158
 
cjtsang@orinvantage.com

Font styles to use
Serif
Sans Serif

Colors

Designer to choose colors to be used in the design.

Requirements
Must have
• APAC Office

```html
<!DOCTYPE html>
<html lang="en">
<head>
<meta charset="utf-8">
<title>Orin Vantage Asia Pacific – Business Card</title>
<link rel="stylesheet" href="https://fonts.googleapis.com/css2?family=Roboto:wght@400;500;700&family=Roboto+Condensed:wght@700&display=swap">
<style>
  :root {
    --backdrop: #2b2b2c;
    --navy: #10294a;
    --cyan: #1fa6d0;
    --paper: #ffffff;
    --ink: #3c3c3c;
    --ink-soft: #4a4a4a;
    --pale: #e9edf1;
  }
  * { margin: 0; padding: 0; box-sizing: border-box; }
  html, body { width: 1200px; height: 960px; overflow: hidden; }
  body {
    background: var(--backdrop);
    font-family: "Roboto", Arial, sans-serif;
    position: relative;
  }

  .card {
    position: absolute;
    left: 320px;
    width: 600px;
    height: 342px;
    overflow: hidden;
  }

  /* Front side */
  .card--front {
    top: 108px;
    background: var(--navy);
  }
  .front-brand {
    position: absolute;
    left: 0; right: 0;
    top: 138px;
    display: flex;
    align-items: center;
    justify-content: center;
    gap: 14px;
  }
  .front-brand__square {
    width: 22px; height: 22px;
    background: var(--pale);
  }
  .front-brand__name {
    font-weight: 700;
    font-size: 34px;
    letter-spacing: 2px;
    color: var(--pale);
  }
  .front-web {
    position: absolute;
    left: 0; right: 0;
    top: 284px;
    text-align: center;
    font-size: 14px;
    letter-spacing: 6.2px;
    color: #cfd6de;
  }

  /* Back side */
  .card--back {
    top: 493px;
    background: var(--paper);
  }
  .back-panel {
    position: absolute;
    left: 0; top: 0;
    width: 600px; height: 342px;
  }
  .back-brand__square {
    position: absolute;
    left: 129px;
    top: 122px;
    width: 24px; height: 24px;
    background: var(--pale);
  }
  .back-brand__name {
    position: absolute;
    left: 0;
    top: 184px;
    width: 282px;
    text-align: center;
    font-weight: 700;
    font-size: 31px;
    line-height: 36px;
    color: var(--cyan);
    white-space: nowrap;
  }

  .holder {
    position: absolute;
    right: 32px;
    top: 26px;
    text-align: right;
  }
  .holder__name {
    font-family: "Roboto Condensed", "Arial Narrow", sans-serif;
    font-weight: 700;
    font-size: 22px;
    color: var(--cyan);
    text-transform: uppercase;
  }
  .holder__title {
    font-size: 15px;
    font-weight: 500;
    color: var(--ink);
    margin-top: 3px;
  }

  .address {
    position: absolute;
    right: 32px;
    top: 128px;
    text-align: right;
    font-size: 14.5px;
    line-height: 19px;
    color: var(--ink-soft);
    font-style: normal;
  }

  .contacts {
    position: absolute;
    right: 32px;
    top: 229px;
    list-style: none;
    font-size: 14.5px;
    line-height: 19.5px;
    color: var(--ink-soft);
  }
  .contacts li {
    display: flex;
    justify-content: flex-end;
    align-items: center;
    gap: 10px;
  }
  .contacts svg { width: 14px; height: 14px; fill: var(--cyan); }
  .voip {
    position: absolute;
    right: 32px;
    top: 296px;
    font-size: 14.5px;
    color: var(--ink-soft);
  }
</style>
</head>
<body>

  <section class="card card--front" aria-label="Business card front">
    <div class="front-brand">
      <span class="front-brand__square"></span>
      <span class="front-brand__name">ORIN VANTAGE</span>
    </div>
    <p class="front-web">www.orinvantage.com</p>
  </section>

  <section class="card card--back" aria-label="Business card back">
    <svg class="back-panel" viewBox="0 0 600 342" aria-hidden="true">
      <polygon points="0,0 202,0 343,171 200,342 0,342" fill="var(--navy)"/>
      <polyline points="202,0 343,171 200,342" fill="none" stroke="var(--cyan)" stroke-width="3"/>
    </svg>

    <span class="back-brand__square"></span>
    <span class="back-brand__name">ORIN VANTAGE</span>

    <div class="holder">
      <h1 class="holder__name">Clara Jo Tsang</h1>
      <p class="holder__title">VP</p>
    </div>

    <address class="address">
      APAC M&amp;A Operations<br>
      Orin Vantage Asia Pacific Limited<br>
      Unit 1407, K18<br>
      18 Tai Lok Shan Road<br>
      Hong Kong
    </address>

    <ul class="contacts">
      <li>+852 2836 4100
        <svg viewBox="0 0 24 24" aria-label="Telephone"><path d="M6.6 10.8a15.1 15.1 0 0 0 6.6 6.6l2.2-2.2c.3-.3.7-.4 1-.2 1.1.4 2.3.6 3.6.6.6 0 1 .4 1 1V20c0 .6-.4 1-1 1A17 17 0 0 1 3 4c0-.6.4-1 1-1h3.5c.6 0 1 .4 1 1 0 1.3.2 2.5.6 3.6.1.3 0 .7-.2 1z"/></svg>
      </li>
      <li>+852 6038 1742
        <svg viewBox="0 0 24 24" aria-label="Mobile"><path d="M7 1h10a2 2 0 0 1 2 2v18a2 2 0 0 1-2 2H7a2 2 0 0 1-2-2V3a2 2 0 0 1 2-2zm0 3v14h10V4zm5 15.5a1 1 0 1 0 0 2 1 1 0 0 0 0-2z"/></svg>
      </li>
      <li>+852 2836 4177
        <svg viewBox="0 0 24 24" aria-label="Fax"><path d="M6 2h12v6H6zM3 9h18a1 1 0 0 1 1 1v7h-4v5H6v-5H2v-7a1 1 0 0 1 1-1zm5 6v5h8v-5z"/></svg>
      </li>
    </ul>

    <p class="voip">VOIP: 4158</p>
  </section>

</body>
</html>
```